New design for existing catalog pages

We want to update and improve our existing design. The existing products on the designs should be adopted. Also the prices, descriptions and article numbers.
It is important that we receive an Indesign file that we can adapt. Also replace the images and adjust texts and prices.

Target Market(s)

Older people with high incomes. More conservative people.

Industry/Entity Type

Münzen und Briefmarkenhandel

Requirements
Must have
• Noble, simple and timeless design that looks high quality.
Nice to have
• The expensive products should be presented accordingly
Should not have
• Don't look cheap. Not too many different and bright colors

```html
<!DOCTYPE html>
<html lang="de">
<head>
<meta charset="utf-8">
<title>Helvetische Republik – Duplonen</title>
<link href="https://fonts.googleapis.com/css2?family=Montserrat:wght@300;400;500;700;800;900&family=Playfair+Display:wght@500;600&display=swap" rel="stylesheet">
<style>
  :root {
    --royal: #1f1fd6;
    --royal-deep: #10108f;
    --ink: #111111;
    --copy: #5a5a5a;
    --paper: #ffffff;
    --silver-light: #f1f3f3;
    --silver-mid: #d3d8d8;
    --silver-dark: #9ea6a6;
    --gold-light: #f6e27a;
    --gold-mid: #e2bd2c;
    --gold-dark: #b98d14;
    --pale-gold-light: #fbf3cf;
    --pale-gold-mid: #ead58a;
  }
  * { box-sizing: border-box; margin: 0; padding: 0; }
  html, body { width: 848px; height: 1200px; overflow: hidden; background: var(--paper); }
  body { position: relative; font-family: "Montserrat", sans-serif; color: var(--ink); }

  .section-tab {
    position: absolute; left: 179px; top: 30px; width: 490px; height: 34px;
    border: 1px solid var(--royal); border-bottom: none; border-radius: 12px 12px 0 0;
    background: var(--paper); text-align: center;
    color: var(--royal); font-size: 23px; font-weight: 400; letter-spacing: 1.2px; line-height: 36px;
  }
  .header-rule { position: absolute; left: 32px; top: 63px; width: 783px; height: 1px; background: var(--royal); }
  .double-rule {
    position: absolute; left: 32px; width: 783px; height: 4px;
    border-top: 1px solid var(--royal); border-bottom: 1px solid var(--royal);
  }
  .rule-top { top: 92px; }
  .rule-bottom { top: 201px; }

  .page-title {
    position: absolute; left: 32px; top: 104px; width: 783px; text-align: center;
    font-family: "Playfair Display", serif; font-weight: 600; color: var(--royal);
    font-size: 36px; line-height: 43px;
  }

  .coin-showcase {
    position: absolute; left: 34px; top: 225px; width: 780px; height: 470px;
    background: radial-gradient(ellipse at 50% 45%, #f7f7f7 0%, #e9e9ea 60%, #f6f6f6 100%);
    border-radius: 0 0 60px 60px;
  }
  .coin {
    position: absolute; border-radius: 50%;
    box-shadow: 6px 10px 18px rgba(0,0,0,.28);
  }
  .coin-reverse {
    left: 473px; top: 273px; width: 304px; height: 304px;
    background: radial-gradient(circle at 40% 35%, var(--gold-light) 0%, var(--gold-mid) 55%, var(--gold-dark) 100%);
  }
  .coin-duplone {
    left: 298px; top: 400px; width: 272px; height: 272px;
    background: radial-gradient(circle at 45% 40%, var(--pale-gold-light) 0%, var(--pale-gold-mid) 70%, #c9ad4f 100%);
  }
  .coin-doppel {
    left: 71px; top: 261px; width: 340px; height: 320px;
    background: radial-gradient(circle at 42% 38%, var(--gold-light) 0%, var(--gold-mid) 55%, var(--gold-dark) 100%);
  }

  .ribbon {
    position: absolute; width: 226px; height: 60px; transform: rotate(-7deg);
    filter: drop-shadow(0 3px 3px rgba(0,0,0,.25));
  }
  .ribbon svg { position: absolute; left: 0; top: 0; }
  .ribbon-label {
    position: absolute; left: 22px; top: 4px; width: 182px; height: 40px;
    display: flex; align-items: center; justify-content: center;
    color: #fff; font-weight: 800; font-size: 16px; letter-spacing: 0.6px;
  }
  .ribbon-rarity { left: 509px; top: 258px; }
  .ribbon-pair { left: 155px; top: 560px; }

  .info-card {
    position: absolute; top: 715px; height: 157px; border-radius: 16px;
    background: linear-gradient(135deg, var(--silver-light) 0%, var(--silver-mid) 55%, #e6eaea 100%);
    border: 2px solid var(--silver-dark);
    box-shadow: 0 6px 10px rgba(0,0,0,.18);
    overflow: hidden; text-align: center;
  }
  .card-doppel { left: 38px; width: 238px; }
  .card-duplone { left: 305px; width: 238px; }
  .card-specs { left: 575px; width: 228px; text-align: left; }

  .card-head {
    height: 92px; border-bottom: 2px solid var(--silver-dark);
    background: linear-gradient(180deg, #eef0f0 0%, #d6dbdb 60%, #e7eaea 100%);
  }
  .card-price { font-weight: 900; font-size: 28px; line-height: 28px; padding-top: 18px; }
  .card-article { font-weight: 700; font-size: 18px; margin-top: 19px; }
  .card-name { font-weight: 700; font-size: 14px; line-height: 17px; padding-top: 16px; }

  .spec-list { list-style: none; padding: 9px 0 0 14px; }
  .spec-list li { font-size: 11.5px; font-weight: 500; line-height: 28.4px; }
  .spec-list li::before { content: "◈"; font-size: 10px; margin-right: 1px; }

  .body-copy {
    position: absolute; top: 912px; width: 250px;
    font-size: 10.9px; font-weight: 300; line-height: 15px; color: var(--copy);
    text-align: justify; hyphens: manual; letter-spacing: 0.1px;
  }
  .body-copy p + p { margin-top: 15px; }
  .col-one { left: 33px; }
  .col-two { left: 299px; }
  .col-three { left: 566px; }

  .footer-rule { position: absolute; left: 32px; width: 783px; height: 1px; background: var(--royal); }
  .fr-1 { top: 1129px; } .fr-2 { top: 1137px; } .fr-3 { top: 1146px; }
  .page-number { position: absolute; left: 0; width: 848px; top: 1161px; text-align: center; font-size: 11px; color: var(--royal); }
  .footer-label { position: absolute; right: 34px; top: 1159px; font-size: 12px; color: var(--royal); letter-spacing: 0.4px; }
</style>
</head>
<body>
  <div class="header-rule"></div>
  <div class="section-tab">HELVETISCHE REPUBLIK - DUPLONEN</div>

  <div class="double-rule rule-top"></div>
  <h1 class="page-title">Duplone und Doppelduplone der Helvetischen<br>Republik 1798 - 1803</h1>
  <div class="double-rule rule-bottom"></div>

  <div class="coin-showcase"></div>
  <div class="coin coin-reverse" role="img" aria-label="Goldmünze, Rückseite mit Bannerträger und Umschrift Helvetische Republik"></div>
  <div class="coin coin-duplone" role="img" aria-label="Duplone 16 Franken 1800 in Gold, Wertseite mit Kranz"></div>
  <div class="coin coin-doppel" role="img" aria-label="Doppelduplone 32 Franken 1800 in Gold, Wertseite mit Kranz"></div>

  <div class="ribbon ribbon-rarity">
    <svg width="226" height="60" viewBox="0 0 226 60" aria-hidden="true">
      <polygon points="0,12 40,14 40,52 12,56 20,32" fill="var(--royal-deep)"/>
      <polygon points="186,4 226,8 210,28 222,48 186,44" fill="var(--royal-deep)"/>
      <rect x="22" y="4" width="182" height="40" fill="var(--royal)"/>
      <rect x="27" y="9" width="172" height="30" fill="none" stroke="#fff" stroke-width="1" stroke-dasharray="2 2"/>
    </svg>
    <div class="ribbon-label">TOP - RARITÄT</div>
  </div>
  <div class="ribbon ribbon-pair">
    <svg width="226" height="60" viewBox="0 0 226 60" aria-hidden="true">
      <polygon points="0,12 40,14 40,52 12,56 20,32" fill="var(--royal-deep)"/>
      <polygon points="186,4 226,8 210,28 222,48 186,44" fill="var(--royal-deep)"/>
      <rect x="22" y="4" width="182" height="40" fill="var(--royal)"/>
      <rect x="27" y="9" width="172" height="30" fill="none" stroke="#fff" stroke-width="1" stroke-dasharray="2 2"/>
    </svg>
    <div class="ribbon-label">DUPLONENPAAR</div>
  </div>

  <div class="info-card card-doppel">
    <div class="card-head">
      <div class="card-price">28900,– CHF</div>
      <div class="card-article">7997.1800.025</div>
    </div>
    <div class="card-name">Helvetische Republik<br>- Doppelduplone 32 Franken</div>
  </div>

  <div class="info-card card-duplone">
    <div class="card-head">
      <div class="card-price">9500,– CHF</div>
      <div class="card-article">7997.1800.015</div>
    </div>
    <div class="card-name">Helvetische Republik<br>- Duplone 16 Franken</div>
  </div>

  <div class="info-card card-specs">
    <ul class="spec-list">
      <li>Schweiz - 16 / 32 Franken</li>
      <li>1800, Helvetische Republik</li>
      <li>7,65 Gramm / 15,26 Gramm - Gold</li>
      <li>23 mm / 29 mm Durchmesser</li>
      <li>vorzüglich bis unzirkuliert</li>
    </ul>
  </div>

  <div class="body-copy col-one">
    <p>Helvetische Republik ist die offizielle Be&shy;zeich&shy;nung des schweizerischen Staats&shy;we&shy;sens, das am 12. April 1798 die alte Eidge&shy;nos&shy;sen&shy;schaft ablöste und bis zum 10. März 1803 bestand.</p>
    <p>Frankreich nutzte die bestehende Unzu&shy;frie&shy;den&shy;heit der ländlichen Eliten in den Unter&shy;ta&shy;nen&shy;ge&shy;bie&shy;ten der alten Eidgenos&shy;sen&shy;schaft, sowie der aufgeklärten Bür&shy;ger in den städtischen Orten und för&shy;derte gezielt revolutionäre Bestrebungen.</p>
  </div>
  <div class="body-copy col-two">
    <p>Angefacht oder ausgelöst und zugleich auch abgesichert wurde die Umwälzung durch französische Truppen, die ab Ende Januar in einer Zangenbewegung von der Waadt und vom Jura her in das westliche Mittelland vorstiessen (Franzoseneinfall). In den Kampfhandlungen Anfang März 1798 ging die alte Eidgenossenschaft unter.</p>
    <p>Einige Städte, allen voran Bern, hatten be&shy;trächt&shy;liche Vermögen in ihren Schatzkam&shy;mern. Der sogenannte Staatsschatz von</p>
  </div>
  <div class="body-copy col-three">
    <p>Bern wurde von den Französischen Trup&shy;pen geplündert. Mehrere Kutschen mit Gold und Silber, sowie die Bären aus dem Bärengraben, wurden nach Paris gekarrt.</p>
    <p>Mit der Einführung der Helvetischen Re&shy;pu&shy;blik ging das Münzwesen von den Kan&shy;to&shy;nen auf den Zentralstaat über und der Franken wurde als Währung festgelegt. In dieser Zeit entstanden die Duplonen (16 Franken) und Doppelduplonen (32 Fran&shy;ken) der Helvetischen Republik.</p>
  </div>

  <div class="footer-rule fr-1"></div>
  <div class="footer-rule fr-2"></div>
  <div class="footer-rule fr-3"></div>
  <div class="page-number">13</div>
  <div class="footer-label">HELVETISCHE REPUBLIK - DUPLONEN</div>
</body>
</html>
```